Business Card Design for Property Development Company Director

I am looking for a professional and unforgettable business card design for our Director of our Property Development Company.
Please see attached .pptx file to find out what information to include. You don't have to follow the exact format shown in the file - I am interested to see your creative flair using the information provided.

```html
<!DOCTYPE html>
<html lang="en">
<head>
<meta charset="utf-8">
<title>Stonevale Property Group – Business Card</title>
<link rel="stylesheet" href="https://fonts.googleapis.com/css2?family=Montserrat:wght@400;500;600&family=Roboto:wght@500;700&display=swap">
<style>
  :root {
    --backdrop: #2b2b2b;
    --card-white: #ffffff;
    --brand-blue: #1059a8;
    --text-grey: #555a60;
    --stripe-grey: #5f6163;
  }
  * { margin: 0; padding: 0; box-sizing: border-box; }
  html, body { width: 1200px; height: 900px; overflow: hidden; background: var(--backdrop); }
  .canvas { position: relative; width: 1200px; height: 900px; }
  .card {
    position: absolute; left: 261px; width: 656px; height: 358px;
    font-family: "Montserrat", sans-serif; overflow: hidden;
  }
  .card--front { top: 69px; background: var(--card-white); }
  .card--back { top: 472px; background: var(--brand-blue); color: #fff; text-align: center; }

  .brand { display: flex; align-items: center; gap: 10px; }
  .brand__mark { width: 30px; height: 30px; }
  .brand__name { font-weight: 600; letter-spacing: 0.04em; text-transform: uppercase; }
  .card--front .brand { position: absolute; left: 26px; top: 46px; }
  .card--front .brand__mark { background: var(--brand-blue); }
  .card--front .brand__name { color: var(--brand-blue); font-size: 22px; }

  .person { position: absolute; right: 27px; top: 176px; text-align: right; }
  .person__name { font-family: "Roboto", sans-serif; font-weight: 700; font-size: 23px; color: var(--brand-blue); line-height: 1.1; }
  .person__role { font-size: 15px; color: var(--text-grey); margin-top: 2px; }

  .divider { position: absolute; left: 25px; right: 27px; top: 233px; height: 1.5px; background: var(--brand-blue); }

  .contacts { position: absolute; left: 25px; top: 257px; list-style: none; }
  .contacts li { display: flex; align-items: center; gap: 6px; font-size: 15px; color: var(--text-grey); height: 21px; }
  .contacts svg { width: 11px; height: 11px; flex: none; }
  .contacts strong { color: var(--brand-blue); font-weight: 500; }

  .address { position: absolute; right: 27px; top: 277px; text-align: right; font-size: 15px; color: var(--text-grey); line-height: 21px; font-style: normal; }

  .footer-band { position: absolute; left: 0; bottom: 0; width: 656px; height: 28px; }

  .tagline { position: absolute; top: 20px; left: 0; right: 0; font-size: 20px; line-height: 28px; font-weight: 400; }
  .card--back .brand { position: absolute; left: 0; right: 0; top: 160px; justify-content: center; }
  .card--back .brand__mark { background: #fff; width: 40px; height: 40px; }
  .card--back .brand__name { color: #fff; font-size: 30px; }
  .invite { position: absolute; left: 0; right: 0; top: 318px; font-size: 17px; font-weight: 500; }
</style>
</head>
<body>
<main class="canvas">
  <section class="card card--front" aria-label="Card front">
    <div class="brand">
      <span class="brand__mark"></span>
      <span class="brand__name">Stonevale Property Group</span>
    </div>

    <div class="person">
      <p class="person__name">DANIEL MERCER</p>
      <p class="person__role">Director</p>
    </div>

    <div class="divider"></div>

    <ul class="contacts">
      <li>
        <svg viewBox="0 0 12 12" aria-hidden="true"><path d="M3 1 L5 3.5 L4 5 Q5 7.5 7 8 L8.5 7 L11 9 L9.5 11 Q3 10.5 1 3 Z" fill="none" stroke="#1059a8" stroke-width="1.2"/></svg>
        0400 218 365
      </li>
      <li>
        <svg viewBox="0 0 12 12" aria-hidden="true"><rect x="1" y="2.5" width="10" height="7" fill="none" stroke="#1059a8" stroke-width="1.2"/><path d="M1 3 L6 6.5 L11 3" fill="none" stroke="#1059a8" stroke-width="1.2"/></svg>
        daniel@stonevale.com.au
      </li>
      <li>
        <svg viewBox="0 0 12 12" aria-hidden="true"><circle cx="6" cy="6" r="5" fill="none" stroke="#1059a8" stroke-width="1.1"/><ellipse cx="6" cy="6" rx="2.2" ry="5" fill="none" stroke="#1059a8" stroke-width="1"/><path d="M1 6 H11 M2 3.5 H10 M2 8.5 H10" stroke="#1059a8" stroke-width="0.9"/></svg>
        <span>www.<strong>stonevale</strong>.com.au</span>
      </li>
    </ul>

    <address class="address">74 Harlow St,<br>Brenton VIC 3072, Australia</address>

    <svg class="footer-band" viewBox="0 0 656 28" preserveAspectRatio="none" aria-hidden="true">
      <path d="M0 8 H380 Q395 8 408 4 Q420 0 440 0 H656 V28 H0 Z" fill="var(--brand-blue)"/>
      <path d="M0 7 H372 Q382 7 390 12 H0 Z" fill="#fff"/>
      <path d="M0 7 H365 Q375 7 382 9 Q365 16 355 16 H0 Z" fill="#fff"/>
      <path d="M0 8 H378 Q368 12 360 12 H0 Z" fill="var(--stripe-grey)"/>
    </svg>
  </section>

  <section class="card card--back" aria-label="Card back">
    <p class="tagline">Property Development<br>&amp; Site Acquisition Specialists</p>
    <div class="brand">
      <span class="brand__mark"></span>
      <span class="brand__name">Stonevale Property Group</span>
    </div>
    <p class="invite">Ask me about our INVESTMENT &amp; PARTNERSHIP opportunities</p>
  </section>
</main>
</body>
</html>
```